ATM BUSINESS MACHINES...

NEED A NEW LOGO AND BUSINESS CARD FOR A BRAND NEW ATM BUSINESS. WE GO TO LOCAL BUSINESSES AND PLACE ATM'S IN THER STORES FOR FREE. IT INCREASES THEIR BUSINESS. A VERY EYE CATCHY LOGO AND COLOR SCHEME...MODERN, PROFESSIONAL, YET MODERN AND APPEALING....

Target Market(s)

alll types of business owners...young & old....

Industry/Entity Type

Business

Contact Information for Business Card

HARBORLINE QUICK FUNDS-ATM'S
" GET YOUR CASH NOW"
Reid T. Walsh
President/Owner
P.O. Box 87
Alder Point, A.P. 29318
hqf.atm@tellwave.net
Free Atm's- Free Instalation, Free Maintenance Never a cost to business owner......Call now to get you free ATM and increase your sales......

Requirements
Nice to have
• $$$ signs.....colors....raised letters....
Maybe a logo HQF $$$ with ATM machine...

```html
<!DOCTYPE html>
<html lang="en">
<head>
<meta charset="utf-8">
<title>Harborline Quick Funds ATM's – Business Card</title>
<link rel="stylesheet" href="https://fonts.googleapis.com/css2?family=Russo+One&family=Roboto+Condensed:wght@700&display=swap">
<style>
  :root {
    --band-red: #d42328;
    --band-red-dark: #c41e24;
    --card-black: #050505;
    --card-charcoal: #2f2f2f;
    --text-white: #ffffff;
    --title-silver: #dcdcdc;
    --title-shade: #6a6a6a;
    --mark-dark: #151515;
    --accent-red: #c9252a;
  }
  * { margin: 0; padding: 0; box-sizing: border-box; }
  html, body { width: 1200px; height: 702px; overflow: hidden; background: #ffffff; }
  .card {
    position: relative;
    width: 1200px;
    height: 702px;
    overflow: hidden;
    background: linear-gradient(90deg, var(--card-black) 0%, #1e1e1e 45%, var(--card-charcoal) 100%);
    font-family: "Roboto Condensed", "Arial Narrow", sans-serif;
    font-weight: 700;
    color: var(--text-white);
  }
  .header-band {
    position: absolute;
    left: 0; top: 0;
    width: 1200px; height: 238px;
    background: linear-gradient(180deg, var(--band-red) 0%, var(--band-red-dark) 100%);
  }
  .brand-mark {
    position: absolute;
    left: 44px; top: 58px;
    width: 158px; height: 196px;
    background: var(--mark-dark);
    display: flex;
    align-items: center;
    justify-content: center;
    font-size: 52px;
    color: var(--text-white);
    letter-spacing: 1px;
  }
  .company-name {
    position: absolute;
    left: 227px; top: 103px;
    font-family: "Russo One", "Arial Black", sans-serif;
    font-weight: 400;
    font-size: 45px;
    line-height: 1.2;
    letter-spacing: 1.2px;
    color: var(--title-silver);
    text-shadow: 0 2px 0 var(--title-shade), 0 3px 3px rgba(0,0,0,0.35);
    white-space: nowrap;
  }
  .tagline {
    position: absolute;
    left: 0; top: 178px;
    width: 1220px;
    text-align: center;
    font-size: 42px;
    line-height: 1;
    color: var(--text-white);
    white-space: nowrap;
  }
  .info-divider {
    position: absolute;
    left: 694px; top: 252px;
    width: 3px; height: 314px;
    background: linear-gradient(180deg, rgba(201,37,42,0) 0%, var(--accent-red) 45%, rgba(201,37,42,0) 100%);
  }
  .contact-block, .person-block {
    position: absolute;
    text-align: center;
    font-size: 34px;
    line-height: 44px;
    white-space: nowrap;
  }
  .contact-block { left: 30px; width: 600px; top: 346px; }
  .person-block { left: 709px; width: 400px; top: 340px; }
  .offer-line {
    position: absolute;
    left: 0; width: 1200px;
    display: flex;
    justify-content: center;
    align-items: center;
    font-size: 34px;
    line-height: 44px;
    white-space: nowrap;
  }
  .offer-line.primary { top: 575px; }
  .offer-line.secondary { top: 623px; left: 14px; }
  .offer-divider {
    display: inline-block;
    width: 3px; height: 48px;
    margin: 0 9px;
    background: linear-gradient(180deg, rgba(201,37,42,0) 0%, var(--accent-red) 50%, rgba(201,37,42,0) 100%);
  }
</style>
</head>
<body>
  <div class="card">
    <div class="header-band"></div>
    <div class="brand-mark">HQF</div>
    <h1 class="company-name">HARBORLINE QUICK FUNDS-ATM'S</h1>
    <p class="tagline">GET YOUR CASH NOW</p>

    <div class="contact-block">
      <p>P.O. Box 87 Alder Point, A.P. 29318</p>
      <p>hqf.atm@tellwave.net</p>
    </div>

    <div class="info-divider"></div>

    <div class="person-block">
      <p>Reid T. Walsh</p>
      <p>President/Owner</p>
    </div>

    <p class="offer-line primary">Free Atm's- Free Instalation<span class="offer-divider"></span>Free Maintenance Never a cost to business owner</p>
    <p class="offer-line secondary">Call now to get you free ATM and increase your sales</p>
  </div>
</body>
</html>
```